Belvascotravel.com web design project + logo design

Hi,

We are a Russian online tour operator - sunkettle.com

We are looking to tranmsfer our domain to belvascotravel.com. The website and logo need to be belvascoesque - we are not looking to change our functionality, but we need to make the website much more attracitve to clients, much more wild looking but at the same time remaining a professional travel company.

The main concept of the website should be innovative travel (as belvasco was an innovator). Alternatively, you could go down the artist route and go down the draw / design your own tour road.

On our website the customer is able to combine travel services (hotels, flights, Visa services, and soon chauffeur, car rental etc...) put it into their basket (the basket definitely has to look better than it is at the moment) and pay for it in one go by card.

We are also stressin our customer support with web chat, call centre etc... (call centre number at the top of the page)

We aim to provide an easy user experience, but we need to make it have some more style, so I will be waiting for what you guys can come up with.
Let me know if you have any questions - skype is: mrdolbarin

Industry/Entity Type

It Company

Requirements
Must have
• It is quite a simple task - to take the existing website sunkettle.com and belvascosize it to create belvascotravel.com, the functionality of the website will remain the same and there are not many pages in the website. Homepage, Checkout step1, Checkout step 2 (you can view both of these if you select a service) and the generic pages for T&C''s, Privacy policy etc...

IMPORTANT UPDATE

We are also looking at how the search results will look in the designs, (please do a search on our website for hotel / flight)

```html
<!DOCTYPE html>
<html lang="fr">
<head>
<meta charset="utf-8">
<title>Belvascotravel.com</title>
<link href="https://fonts.googleapis.com/css2?family=Open+Sans:ital,wght@0,400;0,600;0,700;1,400&family=Ubuntu:wght@300;400;500&display=swap" rel="stylesheet">
<style>
:root{
  --green:#6cb81e;
  --brown:#5b3c38;
  --brown-dark:#4a302d;
  --blue:#2b87cc;
  --phone:#4a7fa8;
  --text:#8a8a8a;
  --dark:#333;
  --footer:#383838;
  --footer-text:#a9a9a9;
  --line:#d9d9d9;
}
*{margin:0;padding:0;box-sizing:border-box}
html,body{width:769px;height:1200px;overflow:hidden;background:#fff}
body{position:relative;font-family:"Open Sans",sans-serif;color:var(--dark)}
.abs{position:absolute}

/* header */
.header{left:0;top:0;width:769px;height:92px;background:#fff}
.logo-box{left:71px;top:0;width:138px;height:101px;background:#fff;z-index:3;display:flex;align-items:center;justify-content:center;gap:5px;padding-top:20px}
.logo-box .dot{width:10px;height:10px;border-radius:50%;background:var(--green)}
.logo-box .name{font-family:"Ubuntu",sans-serif;font-weight:500;font-size:13px;color:var(--brown)}
.social{top:20px;display:flex;gap:6px;left:512px}
.social span{width:16px;height:16px;border-radius:50%;background:#555;display:block}
.social svg{display:block}
.call{left:596px;top:22px;width:106px;text-align:center;font-size:8.5px;line-height:11px;color:var(--phone)}
.nav{left:337px;top:54px;height:25px;display:flex;background:#fff;box-shadow:0 1px 2px rgba(0,0,0,.15)}
.nav a{display:flex;align-items:center;padding:0 13px;font-size:7.5px;color:#333;text-decoration:none;border-right:1px solid #e6e6e6;height:25px;text-transform:uppercase}
.nav a.active{background:var(--green);color:#fff;padding:0 14px}

/* hero */
.hero{left:0;top:92px;width:769px;height:270px;background:linear-gradient(180deg,#5d6aa3 0%,#8a8fc0 35%,#b9a8c8 60%,#3b4a78 80%,#1d2748 100%)}
.tabs{left:91px;top:118px;display:flex;gap:4px}
.tabs span{height:24px;display:flex;align-items:center;padding:0 12px;font-size:10.5px;border-radius:3px 3px 0 0}
.tabs .on{background:var(--green);color:#fff}
.tabs .off{background:#dbe6ef;color:#555;padding:0 13px}
.panel{left:80px;top:142px;width:439px;height:185px;background:rgba(255,255,255,.93);border-radius:2px}
.lbl{font-size:9px;color:#444}
.field{height:18px;background:#eee;border:1px solid #e2e2e2;font-size:7px;color:#aaa;display:flex;align-items:center;padding-left:7px}
.check{font-size:7.5px;color:#555;display:flex;align-items:center;gap:3px}
.check i{width:7px;height:7px;border:1px solid #aaa;display:inline-block;background:#fff;font-style:normal;font-size:6px;line-height:6px;text-align:center}
.btns{left:73px;top:283px;height:33px;display:flex}
.btn{height:33px;display:flex;align-items:center;color:#fff;font-weight:600;font-size:11.5px;background:var(--brown)}
.btn.a{padding:0 10px 0 13px;border-radius:3px 0 0 3px;border-right:1px solid #7a5651}
.btn.b{padding:0 14px 0 11px;font-size:10.5px;clip-path:polygon(0 0,88% 0,100% 50%,88% 100%,0 100%)}

/* services */
.services{left:0;top:362px;width:769px;height:126px;background:#f7f7f7;border-top:2px solid #ddd}
.svc{top:26px;width:130px;text-align:center}
.svc svg{display:block;margin:0 auto;height:28px}
.svc h3{font-weight:400;font-style:italic;font-size:12px;color:var(--brown);margin-top:10px;letter-spacing:.2px}
.svc p{font-size:7.5px;color:var(--text);line-height:10.5px;margin-top:3px}

/* carousel */
.carousel{left:0;top:488px;width:769px;height:123px;background:#000}
.photo{top:14px;width:165px;height:94px;border:2px solid #fff}
.arrow{top:46px}
.down{left:369px;top:595px;width:32px;height:32px;border-radius:50%;background:#000;z-index:2}

/* content */
.tag{left:77px;top:641px;width:91px;height:17px;background:var(--brown);color:#fff;font-size:9.5px;font-weight:600;display:flex;align-items:center;justify-content:center;letter-spacing:.3px}
.rule{left:77px;top:658px;width:620px;height:1px;background:var(--line)}
.ctabs{left:432px;top:645px;display:flex;gap:11px;font-size:7.5px;color:#555}
.ctabs span{padding-bottom:3px}
.ctabs .on{border-bottom:2px solid var(--green)}
.headline{left:79px;top:669px;width:270px;font-family:"Ubuntu",sans-serif;font-weight:300;font-size:18px;line-height:22px;color:var(--blue)}
.body{left:80px;top:739px;width:416px;font-size:7.8px;line-height:14.2px;color:var(--text)}
.list{left:80px;top:852px;list-style:none;font-size:8.2px;color:#444}
.list li{height:14px;display:flex;align-items:center;gap:9px}
.list li b{color:var(--green);font-size:12px;font-weight:400;width:7px}
.dash{top:938px;height:0;border-top:1px dashed #bbb}
.contact-now{left:80px;top:951px;display:flex;align-items:center;gap:9px;font-size:8.5px;font-weight:700;color:var(--brown-dark)}
.contact-now i{width:13px;height:13px;border-radius:50%;background:var(--green);color:#fff;font-style:normal;font-size:12px;line-height:13px;text-align:center}
.side h2{font-family:"Ubuntu",sans-serif;font-weight:400;font-size:16px;color:#333}
.item{display:flex;gap:7px;font-size:8px;line-height:11.6px;color:var(--text);width:165px}
.item a{color:var(--green);text-decoration:none}
.avatar{width:29px;height:29px;flex:none;background:linear-gradient(#c8c8c8,#7a7a7a)}
.date{width:29px;flex:none;text-align:center;color:#333;font-size:14px;line-height:13px;padding-top:4px}
.date sup{font-size:7px}
.date small{display:block;font-size:9px;line-height:11px}

/* footer */
.footer{left:0;top:983px;width:769px;height:182px;background:radial-gradient(ellipse at 50% 0%,#4a4a4a,var(--footer) 60%)}
.notch{left:370px;top:966px;width:30px;height:30px;border-radius:50%;background:#fff;z-index:2}
.flogo{left:82px;top:1018px;display:flex;align-items:center;gap:5px}
.flogo .dot{width:10px;height:10px;border-radius:50%;background:#6a6a6a}
.flogo .name{font-family:"Ubuntu",sans-serif;font-weight:500;font-size:14px;color:#777}
.ftext{font-size:8px;line-height:11.6px;color:var(--footer-text)}
.fhead{font-size:9.5px;font-weight:700;color:#fff;display:flex;align-items:center;gap:8px;width:148px}
.fhead span{flex:1;height:7px;background:repeating-linear-gradient(90deg,#555 0 1px,transparent 1px 2px)}
.fsep{height:1px;background:#4c4c4c}
.fname{font-size:8px;font-weight:700;color:#fff}
.bottom{left:0;top:1165px;width:769px;height:35px;background:#fff;font-size:8px;color:#555}
.bottom nav{position:absolute;left:86px;top:12px;display:flex;gap:11px}
.bottom p{position:absolute;right:80px;top:12px}
</style>
</head>
<body>

<header class="abs header"></header>
<div class="abs logo-box"><span class="dot"></span><span class="name">belvascotravel.com</span></div>
<div class="abs social">
  <span></span><span></span>
  <svg width="16" height="16" viewBox="0 0 16 16"><circle cx="8" cy="8" r="8" fill="#555"/><circle cx="7.3" cy="7.3" r="3" fill="none" stroke="#fff" stroke-width="1.3"/><line x1="9.5" y1="9.5" x2="11.5" y2="11.5" stroke="#fff" stroke-width="1.5"/></svg>
</div>
<div class="abs call">YOU CALL, WE'RE THERE<br>(866-555-0142)</div>
<nav class="abs nav">
  <a class="active">Home</a><a>Destinations</a><a>Activites</a><a>Trip Styles</a><a style="border:0">Responsible Travel</a>
</nav>

<section class="abs hero" role="img" aria-label="Evening photo of a luxury seaside hotel under a purple sky"></section>

<div class="abs tabs"><span class="on">сторону</span><span class="off">Класс</span></div>
<form class="abs panel">
  <span class="abs lbl" style="left:10px;top:20px">Откуда</span>
  <span class="abs field" style="left:56px;top:16px;width:155px">Enter Zip / Postal Code</span>
  <span class="abs lbl" style="left:219px;top:20px">Куда</span>
  <span class="abs field" style="left:249px;top:16px;width:136px">Enter Zip / Postal Code</span>

  <span class="abs lbl" style="left:10px;top:51px">Туда</span>
  <span class="abs field" style="left:56px;top:48px;width:107px">Enter Zip</span>
  <span class="abs lbl" style="left:176px;top:52px">Обратно</span>
  <span class="abs field" style="left:218px;top:49px;width:110px">Enter Zip</span>
  <span class="abs check" style="left:337px;top:47px"><i></i>Обратно</span>
  <span class="abs check" style="left:337px;top:59px"><i>✓</i>В одну сторону</span>

  <span class="abs lbl" style="left:10px;top:82px">Пассажиры</span>
  <svg class="abs" style="left:82px;top:78px" width="8" height="18" viewBox="0 0 8 18"><circle cx="4" cy="2" r="2" fill="#222"/><rect x="1" y="5" width="6" height="13" rx="1" fill="#222"/></svg>
  <span class="abs field" style="left:97px;top:80px;width:46px">Enter Zip</span>
  <svg class="abs" style="left:178px;top:82px" width="6" height="13" viewBox="0 0 6 13"><circle cx="3" cy="1.5" r="1.5" fill="#222"/><rect x="1" y="4" width="4" height="9" rx="1" fill="#222"/></svg>
  <span class="abs field" style="left:192px;top:80px;width:46px">Enter Zip</span>
  <svg class="abs" style="left:265px;top:84px" width="8" height="10" viewBox="0 0 8 10"><circle cx="4" cy="1.5" r="1.5" fill="#222"/><rect x="1.5" y="4" width="5" height="6" rx="1" fill="#222"/></svg>
  <span class="abs field" style="left:285px;top:80px;width:46px">Enter Zip</span>

  <span class="abs lbl" style="left:10px;top:113px">Класс</span>
  <span class="abs field" style="left:54px;top:111px;width:78px">Enter Zip</span>
</form>
<div class="abs btns"><span class="btn a">Check Availability</span><span class="btn b">View Basket</span></div>

<section class="abs services">
  <div class="abs svc" style="left:68px">
    <svg viewBox="0 0 30 28" width="30"><rect x="7" y="3" width="16" height="22" rx="2" fill="#222"/><circle cx="15" cy="12" r="4" fill="none" stroke="#f7f7f7" stroke-width="1.3"/><rect x="10" y="19" width="10" height="1.5" fill="#f7f7f7"/></svg>
    <h3>VISA SERVICE</h3><p>Lorem Ipsum est simplement du<br>faux texte employé.</p>
  </div>
  <div class="abs svc" style="left:232px">
    <svg viewBox="0 0 60 28" width="60"><path d="M4 17 L50 8 Q58 7 56 11 Q54 14 46 15 L30 18 L20 26 L15 26 L21 19 L10 21 L6 25 L3 25 L5 19 Z" fill="#222"/></svg>
    <h3>FLIGHT SERVICE</h3><p>Lorem Ipsum est simplement du<br>faux texte employé.</p>
  </div>
  <div class="abs svc" style="left:400px">
    <svg viewBox="0 0 36 28" width="36"><rect x="2" y="5" width="3" height="20" fill="#222"/><rect x="31" y="10" width="3" height="15" fill="#222"/><rect x="2" y="15" width="32" height="5" fill="#222"/><rect x="7" y="10" width="6" height="4" rx="1" fill="#222"/><rect x="14" y="11" width="17" height="3" fill="#222"/></svg>
    <h3>HOTELS SERVICE</h3><p>Lorem Ipsum est simplement du<br>faux texte employé.</p>
  </div>
  <div class="abs svc" style="left:565px">
    <svg viewBox="0 0 56 28" width="56"><path d="M3 20 Q3 14 10 13 L17 7 Q20 5 26 5 L34 5 Q38 5 42 9 L46 13 Q53 14 53 19 L53 21 L3 21 Z" fill="#222"/><rect x="19" y="8" width="7" height="5" fill="#f7f7f7"/><rect x="28" y="8" width="8" height="5" fill="#f7f7f7"/><circle cx="14" cy="21" r="4.5" fill="#222" stroke="#f7f7f7" stroke-width="1.5"/><circle cx="42" cy="21" r="4.5" fill="#222" stroke="#f7f7f7" stroke-width="1.5"/></svg>
    <h3>RENTAL CAR SERVICE</h3><p>Lorem Ipsum est simplement du<br>faux texte employé.</p>
  </div>
</section>

<section class="abs carousel">
  <svg class="abs arrow" style="left:72px" width="26" height="30" viewBox="0 0 26 30"><path d="M22 2 L6 15 L22 28" fill="none" stroke="#fff" stroke-width="6"/></svg>
  <div class="abs photo" style="left:110px;background:linear-gradient(180deg,#9fd0ee 0%,#6db4d8 40%,#e9d7b0 65%,#d8c290 100%)" role="img" aria-label="Family playing on a sunny beach"></div>
  <div class="abs photo" style="left:303px;background:linear-gradient(180deg,#5a9de0 0%,#a9cde8 45%,#6a99b8 60%,#dcd0b4 100%)" role="img" aria-label="Family cheering on the beach with arms raised"></div>
  <div class="abs photo" style="left:496px;background:linear-gradient(135deg,#f1f1f1 0%,#d95a63 40%,#e8c9a8 70%,#f4f4f4 100%)" role="img" aria-label="Smiling family with luggage in front of an airplane"></div>
  <svg class="abs arrow" style="left:672px" width="26" height="30" viewBox="0 0 26 30"><path d="M4 2 L20 15 L4 28" fill="none" stroke="#fff" stroke-width="6"/></svg>
</section>
<div class="abs down"><svg width="32" height="32" viewBox="0 0 32 32"><path d="M11 16 L16 21 L21 16" fill="none" stroke="#fff" stroke-width="1.5"/></svg></div>

<div class="abs tag">HOW TO DO</div>
<div class="abs rule"></div>
<div class="abs ctabs"><span class="on">VISA SERVICE</span><span>FLIGHT SERVICE</span><span>HOTEL SERVICES</span><span>OTHER SERVICES</span></div>

<h1 class="abs headline" style="font-weight:300">Lorem Ipsum est simplement du faux texte employé dans la sition page avant impression.</h1>
<p class="abs body">Lorem Ipsum est simplement du faux texte employé dans la sition et la misen page avant impression. Le Lorem Ipsum est le faux texte standard de l'imprimerie depuis les années 1500, quand un peintre anonyme assembla ensemble des morceaux de texte pour réaliser un livre spécimen de polices de texte. Il n'a pas fait que survivre cinq siècles, mais s'est aussi adapté à la bureautique informatique, sans que son contenu n'en soit modifié. Il a été popularisé dans les années 1960 grâce à la vente de feuilles Transfera contenant des passages du Lorem Ipsum, et, plus récemment, par son inclusion dans des applications de mise en page de texte, comme Quillset Layout.</p>
<ul class="abs list">
  <li><b>+</b>Morceaux de texte pour réaliser un livre spécimen</li>
  <li><b>+</b>Polices de texte. Il n'a pas fait que survivre cinq siècles</li>
  <li><b>+</b>Mais s'est aussi adapté à la bureautique informatique</li>
  <li><b>+</b>Popularisé dans les années 1960 grâce à la vente de</li>
  <li><b>+</b>Feuilles Transfera contenant des passages du Lorem</li>
</ul>
<div class="abs dash" style="left:77px;width:220px"></div>
<div class="abs dash" style="left:328px;width:312px"></div>
<div class="abs contact-now">CONTACT US NOW <i>+</i></div>

<aside class="abs side" style="left:534px;top:670px">
  <h2>Testimonials</h2>
  <div class="item" style="margin-top:9px"><span class="avatar" role="img" aria-label="Customer portrait"></span><p>Lorem ipsum dolor sit nsectetuer adipiscing elit, sed diam nummy nibh euismod. <a>Read More</a></p></div>
  <div class="item" style="margin-top:12px"><span class="avatar" role="img" aria-label="Customer portrait"></span><p>Lorem ipsum dolor sit nsectetuer adipiscing elit, sed diam nummy nibh euismod. <a>Read More</a></p></div>
  <h2 style="margin-top:34px">Recent News</h2>
  <div class="item" style="margin-top:6px"><span class="date">14<sup>th</sup><small>Jun</small></span><p>Lorem ipsum dolor sit nsectetuer adipiscing elit, sed diam nummy nibh euismod. <a>Read More</a></p></div>
  <div class="item" style="margin-top:12px"><span class="date">10<sup>th</sup><small>Jun</small></span><p>Lorem ipsum dolor sit nsectetuer adipiscing elit, sed diam nummy nibh euismod. <a>Read More</a></p></div>
</aside>

<footer class="abs footer"></footer>
<div class="abs notch"><svg width="30" height="30" viewBox="0 0 30 30"><path d="M10 19 L15 24 L20 19" fill="none" stroke="#444" stroke-width="1.3"/></svg></div>

<div class="abs flogo"><span class="dot"></span><span class="name">belvascotravel.com</span></div>
<div class="abs ftext" style="left:82px;top:1068px;width:125px">Le Lorem Ipsum est simplement faux texte employé page. pssion. Lorem Ipsum</div>
<div class="abs ftext" style="left:84px;top:1114px;width:125px">l'imprimerie depuis les années 1500, quand un peintre .</div>

<div class="abs fhead" style="left:229px;top:1013px">LATEST NEWS <span></span></div>
<div class="abs ftext" style="left:230px;top:1041px;width:140px">Le Lorem Ipsum est simplement.</div>
<div class="abs fsep" style="left:229px;top:1060px;width:140px"></div>
<div class="abs ftext" style="left:230px;top:1070px;width:125px">Le Lorem Ipsum est simplement faux texte employé page.</div>
<div class="abs fsep" style="left:229px;top:1103px;width:140px"></div>
<div class="abs ftext" style="left:230px;top:1113px;width:125px">Le Lorem Ipsum est simplement faux texte employé page.</div>

<div class="abs fhead" style="left:382px;top:1013px">TESTIMONIALS <span></span></div>
<div class="abs ftext" style="left:384px;top:1041px;width:140px">"Le Lorem Ipsum est simplement faux texte employé page."</div>
<div class="abs fname" style="left:384px;top:1068px">Marlon Fenwick</div>
<div class="abs fsep" style="left:382px;top:1083px;width:140px"></div>
<div class="abs ftext" style="left:384px;top:1091px;width:140px">Le Lorem Ipsum est simplement faux texte employé page. pression. Lorem Ipsum</div>
<div class="abs fname" style="left:384px;top:1129px">Marlon Fenwick</div>

<div class="abs fhead" style="left:535px;top:1013px;width:142px">CONTACT US <span></span></div>
<div class="abs ftext" style="left:537px;top:1037px;line-height:11.6px"><b style="color:#fff">Email</b><br><b style="color:#fff">Tel</b><br><b style="color:#fff">Fax</b></div>
<div class="abs ftext" style="left:569px;top:1037px">hello@belvascotravel.com<br>+12 555 0190<br>+12 555 0190</div>
<div class="abs fname" style="left:537px;top:1091px;font-size:9px">Belvascotravel</div>
<div class="abs ftext" style="left:537px;top:1104px">345 Some Street, City,<br>Country<br>Postal Code</div>

<div class="abs bottom">
  <nav><span>Home</span><span>About Us</span><span>Services</span><span>News Matter</span><span>Resources</span><span>Blog</span></nav>
  <p>Copyright 2012 Website Name. All Rights Reserved.</p>
</div>

</body>
</html>
```